One of a Kind Clean Business Card

We need to design a new business card template for our company. Our company designs and produced merchandising displays. You can see a sample of what we produce on our site www.qorvanexhibits.net. I have uploaded our logo in vector format, as well as a picture of our current business cards. We want a totally different look. We want simple and clean, looking forward to seeing what people create.
Updates

I would like to update the address for Qorvan Display Group Inc. 518 E Tollmere Ln Arlington Heights, IL 60017 Would also note. No QR codes

Industry/Entity Type

Business

Contact Information for Business Card

Need a 1 sided business card designed.

Font styles to use
Serif

Requirements
Must have
• Easy to view; Clean Design
Nice to have
• Features that promote engineering and creativity
Should not have
• Too much clutter, keep it simple

```html
<!DOCTYPE html>
<html lang="en">
<head>
<meta charset="utf-8">
<title>Qorvan Display Group Inc. – Business Card</title>
<link href="https://fonts.googleapis.com/css2?family=Source+Serif+4:opsz,wght@8..60,400;8..60,500&display=swap" rel="stylesheet">
<style>
  :root {
    --backdrop: #e9e7e4;
    --card-black: #060606;
    --card-red: #8a0509;
    --panel-white: #ffffff;
    --ink-light: #ffffff;
    --accent-red: #c4262c;
    --brand-red: #8a0509;
  }
  * { margin: 0; padding: 0; box-sizing: border-box; }
  html, body {
    width: 1200px; height: 900px; overflow: hidden;
    background: var(--backdrop);
    font-family: "Source Serif 4", Georgia, serif;
  }
  .business-card {
    position: absolute; left: 100px; top: 141px;
    width: 1000px; height: 618px;
    background: var(--card-red);
    overflow: hidden;
    box-shadow: 0 10px 30px rgba(0,0,0,0.18);
  }
  .top-band {
    position: absolute; left: 0; top: 0; width: 1000px; height: 292px;
    background: var(--card-black);
  }
  .brand-panel-tab {
    position: absolute; left: 46px; top: 169px; width: 243px; height: 124px;
    background: var(--panel-white);
  }
  .brand-panel-band {
    position: absolute; left: 46px; top: 292px; width: 954px; height: 151px;
    background: var(--panel-white);
  }
  .holder-name {
    position: absolute; left: 69px; top: 68px;
    color: var(--ink-light); font-size: 36px; font-weight: 400; letter-spacing: 0.5px;
    line-height: 48px;
  }
  .contact-list {
    position: absolute; right: 52px; top: 111px;
    list-style: none; text-align: right;
  }
  .contact-list li {
    display: flex; justify-content: flex-end; align-items: center;
    height: 37.5px; color: var(--ink-light); font-size: 25px; line-height: 1;
  }
  .contact-list svg { width: 20px; height: 20px; margin-left: 12px; fill: var(--accent-red); flex: none; }
  .brand-name {
    position: absolute; left: 92px; top: 330px;
    color: var(--brand-red); font-size: 38px; font-weight: 400; letter-spacing: 0.5px;
    line-height: 48px; white-space: nowrap;
  }
  .street-address {
    position: absolute; right: 54px; top: 494px;
    color: var(--ink-light); font-size: 25px; line-height: 38px; text-align: right;
    font-style: normal; white-space: nowrap;
  }
</style>
</head>
<body>
  <div class="business-card">
    <div class="top-band"></div>
    <div class="brand-panel-tab"></div>
    <div class="brand-panel-band"></div>

    <div class="holder-name">DALE ORVIK</div>

    <ul class="contact-list">
      <li>815-555-0142
        <svg viewBox="0 0 20 20" aria-hidden="true"><path d="M2 7c0-3 3-4 8-4s8 1 8 4v2h-4V7H6v2H2z"/><path d="M4 11h12l1 6H3z"/></svg>
      </li>
      <li>312-555-0187
        <svg viewBox="0 0 20 20" aria-hidden="true"><path d="M6 1h8a1 1 0 0 1 1 1v16a1 1 0 0 1-1 1H6a1 1 0 0 1-1-1V2a1 1 0 0 1 1-1zm1 2v12h6V3zm3 13a1 1 0 1 0 0 2 1 1 0 0 0 0-2z"/></svg>
      </li>
      <li>dorvik@qorvanexhibits.net
        <svg viewBox="0 0 20 20" aria-hidden="true"><path d="M2 4h16v12H2zm1.5 1.5L10 11l6.5-5.5z"/></svg>
      </li>
      <li>www.qorvanexhibits.net
        <svg viewBox="0 0 20 20" aria-hidden="true"><circle cx="10" cy="10" r="8"/></svg>
      </li>
    </ul>

    <div class="brand-name">Qorvan Display Group Inc.</div>

    <address class="street-address">518 E Tollmere Ln<br>Arlington Heights, IL 60017</address>
  </div>
</body>
</html>
```